Corvin Ridge Software PowerPoint template

We are a software company selling endpoint visibility, access and security technology to enterprise-level IT departments.
Our technology helps organizations gain comprehensive visibility into and control over devices accessing their corporate network so they can quickly identify and address suspicious activity on the network that could lead to potential threats like data breaches.
This technology can cost organizations upwards of $1M - depending on the size of the organization. Our primary clients are Vestral 2,000 companies.
We want a professional, polished PowerPoint template that we can use for all company presentations. Please include:
Title page
Section page
General info page
Thank you page
Logo options and color specs are attached.
Please include our tagline on at least the title page: Discover the edge. Optimize the whole.
Reason: Seeking more options. Looking for a clean design that uses lots of white space.
Software

```html
<!DOCTYPE html>
<html lang="en">
<head>
<meta charset="utf-8">
<title>Corvin Ridge Software — General Info Slide</title>
<link rel="stylesheet" href="https://fonts.googleapis.com/css2?family=Roboto+Condensed:wght@400;700&family=Roboto:wght@400;500&display=swap">
<style>
  :root {
    --brand-red: #951b1b;
    --accent-orange: #f0845a;
    --rule-orange: #e9a27a;
    --heading-red: #8f1b1b;
    --body-text: #444444;
    --footer-grey: #595959;
    --paper: #ffffff;
    --mist: #ececec;
  }
  * { margin: 0; padding: 0; box-sizing: border-box; }
  html, body {
    width: 1200px; height: 900px; overflow: hidden; background: var(--paper);
  }
  .slide {
    position: relative; width: 1200px; height: 900px; overflow: hidden;
    background: var(--paper);
    font-family: "Roboto", Arial, sans-serif;
  }
  .slide-header {
    position: absolute; left: 0; top: 0; width: 1200px; height: 100px;
    background: var(--brand-red);
    border-bottom: 3px solid var(--rule-orange);
  }
  .slide-title {
    position: absolute; left: 24px; top: 22px;
    font-family: "Roboto Condensed", "Arial Narrow", sans-serif;
    font-weight: 700; font-size: 48px; line-height: 56px;
    color: var(--paper); letter-spacing: 0;
  }
  .slide-title .title-accent { color: var(--accent-orange); }
  .brand {
    position: absolute; right: 26px; top: 32px;
    display: flex; align-items: center; gap: 12px;
  }
  .brand-mark { width: 14px; height: 14px; background: var(--paper); }
  .brand-name {
    font-family: "Roboto Condensed", "Arial Narrow", sans-serif;
    font-weight: 400; font-size: 22px; line-height: 30px;
    letter-spacing: 3px; text-transform: uppercase; color: var(--paper);
  }
  .side-texture {
    position: absolute; left: 0; top: 170px; width: 290px; height: 620px;
    background: radial-gradient(ellipse at 0% 50%, var(--mist) 0%, rgba(236,236,236,0.5) 40%, rgba(255,255,255,0) 75%);
  }
  .info-block { position: absolute; left: 48px; width: 1080px; }
  .info-block--one { top: 186px; }
  .info-block--two { top: 367px; }
  .info-block--three { top: 578px; }
  .info-heading {
    display: flex; align-items: center; gap: 9px;
    font-family: "Roboto Condensed", "Arial Narrow", sans-serif;
    font-weight: 700; font-size: 24px; line-height: 32px;
    color: var(--heading-red);
  }
  .info-heading svg { width: 18px; height: 24px; flex: none; }
  .info-body {
    margin-top: 8px; padding-left: 27px;
    font-size: 18px; line-height: 30px; color: var(--body-text);
  }
  .info-body span { display: block; white-space: nowrap; }
  .slide-footer {
    position: absolute; left: 0; bottom: 0; width: 1200px; height: 42px;
    background: var(--footer-grey); color: var(--paper);
    font-family: "Roboto", Arial, sans-serif; font-size: 17px; line-height: 42px;
    display: flex; justify-content: space-between; padding: 0 14px 0 10px;
  }
</style>
</head>
<body>
<div class="slide">
  <header class="slide-header">
    <h1 class="slide-title">PROJECT <span class="title-accent">TITLE HERE</span></h1>
    <div class="brand">
      <span class="brand-mark"></span>
      <span class="brand-name">Corvin Ridge Software</span>
    </div>
  </header>

  <div class="side-texture" role="img" aria-label="Soft grey background texture along the left edge"></div>

  <section class="info-block info-block--one">
    <h2 class="info-heading">
      <svg viewBox="0 0 18 24" aria-hidden="true"><path d="M2 3 L16 12 L2 21 Z" fill="var(--heading-red)"/></svg>
      Subtitle Here
    </h2>
    <p class="info-body">
      <span>Lorem ipsum dolor sit Lorem ipsum dolor sit&nbsp; Lorem ipsum dolor sit Lorem ipsum dolor sit&nbsp; Lorem ipsum dolor sit Lorem ipsum</span>
      <span>dolor sit&nbsp; Lorem ipsum dolor sit Lorem ipsum dolor sit&nbsp; Lorem ipsum dolor sit Lorem ipsum dolor sit&nbsp; Lorem ipsum dolor sit Lorem</span>
      <span>ipsum dolor sit&nbsp; Lorem ipsum dolor sit Lorem ipsum dolor sit&nbsp; Lorem ipsum dolor sit Lorem ipsum dolor sit</span>
    </p>
  </section>

  <section class="info-block info-block--two">
    <h2 class="info-heading">
      <svg viewBox="0 0 18 24" aria-hidden="true"><path d="M2 3 L16 12 L2 21 Z" fill="var(--heading-red)"/></svg>
      Subtitle Here
    </h2>
    <p class="info-body">
      <span>Lorem ipsum dolor sit Lorem ipsum dolor sit&nbsp; Lorem ipsum dolor sit Lorem ipsum dolor sit&nbsp; Lorem ipsum dolor sit Lorem ipsum</span>
      <span>dolor sit&nbsp; Lorem ipsum dolor sit Lorem ipsum dolor sit&nbsp; Lorem ipsum dolor sit Lorem ipsum dolor sit&nbsp; Lorem ipsum dolor sit Lorem</span>
      <span>ipsum dolor sit&nbsp; Lorem ipsum dolor sit Lorem ipsum dolor sit&nbsp; Lorem ipsum dolor sit Lorem ipsum dolor sit</span>
    </p>
  </section>

  <section class="info-block info-block--three">
    <h2 class="info-heading">
      <svg viewBox="0 0 18 24" aria-hidden="true"><path d="M2 3 L16 12 L2 21 Z" fill="var(--heading-red)"/></svg>
      Subtitle Here
    </h2>
    <p class="info-body">
      <span>Lorem ipsum dolor sit Lorem ipsum dolor sit&nbsp; Lorem ipsum dolor sit Lorem ipsum dolor sit&nbsp; Lorem ipsum dolor sit Lorem ipsum</span>
      <span>dolor sit&nbsp; Lorem ipsum dolor sit Lorem ipsum dolor sit&nbsp; Lorem ipsum dolor sit Lorem ipsum dolor sit&nbsp; Lorem ipsum dolor sit Lorem</span>
      <span>ipsum dolor sit&nbsp; Lorem ipsum dolor sit Lorem ipsum dolor sit&nbsp; Lorem ipsum dolor sit Lorem ipsum dolor sit</span>
    </p>
  </section>

  <footer class="slide-footer">
    <span class="footer-copyright">COPYRIGHT TEXT HERE</span>
    <span class="footer-page">Page : 01</span>
  </footer>
</div>
</body>
</html>
```